The quiet harbor with an elephant incorporated in the background

Target Market(s)

Real estate

Industry/Entity Type

Real Estate

Contact Information for Business Card

On back on want my name & number
In front I want the business name, "the quiet harbor", below to say staging & design

Logo Text

The quiet harbor

Font styles to use
Serif

Colors
000000

Requirements
Must have
• I want an elephant behind the writing in gold transperant

```html
<!DOCTYPE html>
<html lang="en">
<head>
<meta charset="utf-8">
<title>The Quiet Harbor – Business Card</title>
<link href="https://fonts.googleapis.com/css2?family=Cormorant+Garamond:wght@400;500;600;700&display=swap" rel="stylesheet">
<style>
  :root {
    --canvas-bg: #e6e6e6;
    --card-white: #ffffff;
    --band-black: #222222;
    --ink: #2b2b2b;
    --ink-soft: #3a3a3a;
    --band-text: #ffffff;
    --band-text-soft: #d9c48a;
    --gold-light: rgba(242, 204, 85, 0.55);
    --gold-mid: rgba(217, 166, 42, 0.38);
    --gold-fade: rgba(217, 166, 42, 0);
  }
  * { margin: 0; padding: 0; box-sizing: border-box; }
  html, body {
    width: 1200px;
    height: 1000px;
    overflow: hidden;
  }
  body {
    background: var(--canvas-bg);
    font-family: "Cormorant Garamond", Georgia, serif;
    position: relative;
  }
  .card {
    position: absolute;
    top: 352px;
    width: 520px;
    height: 297px;
    background: var(--card-white);
    box-shadow: 0 2px 6px rgba(0,0,0,0.25);
    overflow: hidden;
  }
  .card--back { left: 60px; }
  .card--front { left: 620px; }

  .holder-name {
    position: absolute;
    inset: 0;
    display: flex;
    align-items: center;
    justify-content: center;
    font-size: 27px;
    letter-spacing: 5px;
    color: var(--ink);
  }
  .holder-name__first { font-weight: 700; margin-right: 12px; }
  .holder-name__last { font-weight: 500; }

  .brand-band {
    position: absolute;
    left: 0; top: 0; bottom: 0;
    width: 78px;
    background: var(--band-black);
    z-index: 2;
  }
  .brand-band__text {
    position: absolute;
    left: 0;
    top: 297px;
    width: 297px;
    height: 78px;
    transform-origin: top left;
    transform: rotate(-90deg);
    display: flex;
    flex-direction: column;
    justify-content: center;
    padding-left: 22px;
    gap: 2px;
  }
  .brand-band__name {
    color: var(--band-text);
    font-size: 22px;
    font-weight: 600;
    line-height: 1;
    white-space: nowrap;
  }
  .brand-band__tagline {
    color: var(--band-text-soft);
    font-size: 12px;
    font-weight: 600;
    letter-spacing: 2px;
    text-transform: uppercase;
    line-height: 1.2;
    white-space: nowrap;
  }

  .elephant-figure {
    position: absolute;
    left: 150px;
    top: 18px;
    width: 340px;
    height: 268px;
    border-radius: 50%;
    background: radial-gradient(ellipse at 50% 45%, var(--gold-light) 0%, var(--gold-mid) 45%, var(--gold-fade) 72%);
    z-index: 0;
  }
  .contact-line {
    position: absolute;
    left: 78px;
    right: 0;
    bottom: 22px;
    text-align: center;
    font-size: 14px;
    font-weight: 600;
    letter-spacing: 0.5px;
    color: var(--ink-soft);
    z-index: 1;
  }
</style>
</head>
<body>
  <section class="card card--back" aria-label="Card back">
    <p class="holder-name">
      <span class="holder-name__first">DANIEL</span>
      <span class="holder-name__last">HART</span>
    </p>
  </section>

  <section class="card card--front" aria-label="Card front">
    <div class="elephant-figure" role="img" aria-label="Transparent gold elephant figurine behind the text"></div>
    <div class="brand-band">
      <div class="brand-band__text">
        <span class="brand-band__name">The Quiet Harbor</span>
        <span class="brand-band__tagline">Staging &amp; Design</span>
      </div>
    </div>
    <p class="contact-line">000 000 0000 | info@yourmail.com | www.yourweb.com</p>
  </section>
</body>
</html>
```